Counseling Practice Business Card

I need a professional looking business card incorporating my new logo that was just completed. Card needs to incorporate my name and title, description of my specialty, my address, my phone number, my fax number, my email and my website URL. I need to be able to choose design on/with different paper colors and textures.
I do not have a lot of business card ideas so I am open to anything but I want bold,sharp, clear card without additional designs other than my logo (see attached file info). I am open to different color backgrounds or paper colors including black. I do not like traditional brackets around area codes in phone number or dashes between numbers in phone number. Am open to other ways of presenting including periods between numbers as appropriate. I do not know enough to know what I like yet but I want card to coordinate and work together with my logo. My practice emphasizes natural mental health interventions so any use of color (with background paper color or the blue and green in my logo) that elicits nature is nice. In addition to black, any natural brown or wood looking background might be desirable also. Most of the offerings so far look very similar and boring.

Target Market(s)

Potential therapy clients and other professionals

Contact Information for Business Card

Card information:
Gerald M. Whitcombe, Ph.D.
Licensed Clinical Psychologist
Integrative Health Coach
4812 Marlowe Ridge Blvd SE
Suite 310
Duluth, GA 30096
(770) 415-2983 phone
(770) 581-4096 fax
drgeraldwhitcombe@quillmarsh.net
brightfernwellness.net

Font styles to use
Serif
Sans Serif
Other font styles liked:
• anything that you think looks crisp, clear and easily readable

Requirements
Must have
• Any color used should coordinate with my logo design (see attached files).
• Card should be printed horizontally so top and bottom are longest sides of rectangle.
• Background color or paper color should complement and highlight logo. Do not like a white background. black, grey, brown or any color my logo would blend well with.
Nice to have
• I would like designer to utilize color to highlight letters/name or phone-fax-web symbols.
• Bottom edge of card could be highlighted if appropriate to an idea.
Should not have
• I would NOT want the card to have a pure white background at all.
• No clear cards.
• Cards should be oriented with long sides on bottom and top, NOT sides. DO NOT LIKE THIS THIN TALL ORIENTATION.

```html
<!DOCTYPE html>
<html lang="en">
<head>
<meta charset="utf-8">
<title>Brightfern Wellness – Business Card</title>
<link href="https://fonts.googleapis.com/css2?family=Roboto:wght@400;500;700&display=swap" rel="stylesheet">
<style>
  :root {
    --backdrop: #3b3b3d;
    --card: #1d1e21;
    --emboss: #4a4b4f;
    --brand-blue: #2f86c8;
    --text-light: #e6e6e6;
    --text-muted: #c9c9c9;
  }
  * { margin: 0; padding: 0; box-sizing: border-box; }
  html, body { width: 799px; height: 1200px; overflow: hidden; }
  body {
    background: var(--backdrop);
    font-family: "Roboto", Arial, sans-serif;
    position: relative;
  }
  .card {
    position: absolute;
    left: 60px;
    width: 679px;
    height: 388px;
    background: var(--card);
    border-radius: 4px;
    box-shadow: 0 14px 30px rgba(0,0,0,0.45);
    overflow: hidden;
  }
  .card--front { top: 110px; }
  .card--back { top: 700px; }

  .brand-name {
    font-family: "Roboto", Arial, sans-serif;
    font-weight: 500;
    white-space: nowrap;
  }
  .card--front .brand {
    position: absolute;
    left: 0; right: 0; top: 160px;
    text-align: center;
  }
  .card--front .brand-name {
    font-size: 52px;
    color: var(--emboss);
  }

  .card--back .brand {
    position: absolute;
    left: 36px; top: 150px;
  }
  .card--back .brand-name {
    font-size: 34px;
    color: var(--brand-blue);
    line-height: 1.1;
  }

  .contact {
    position: absolute;
    left: 362px; top: 78px;
    right: 20px;
    color: var(--text-light);
  }
  .contact .person {
    font-size: 19px;
    font-weight: 700;
    color: var(--brand-blue);
    white-space: nowrap;
  }
  .contact .role {
    font-size: 13px;
    line-height: 1.35;
    color: var(--text-muted);
    margin-top: 4px;
  }
  .contact .address {
    font-size: 14px;
    line-height: 1.35;
    margin-top: 14px;
  }
  .contact ul {
    list-style: none;
    margin-top: 10px;
    font-size: 14px;
    line-height: 1.5;
  }
  .contact li {
    display: flex;
    align-items: center;
    gap: 9px;
    white-space: nowrap;
  }
  .contact li svg {
    width: 12px; height: 12px;
    fill: var(--brand-blue);
    flex: none;
  }
</style>
</head>
<body>
  <section class="card card--front">
    <div class="brand"><span class="brand-name">Brightfern Wellness</span></div>
  </section>

  <section class="card card--back">
    <div class="brand"><span class="brand-name">Brightfern<br>Wellness</span></div>
    <div class="contact">
      <p class="person">Gerald M. Whitcombe, Ph.D.</p>
      <p class="role">Licensed Clinical Psychologist<br>Integrative Health Coach</p>
      <p class="address">4812 Marlowe Ridge Blvd SE<br>Suite 310<br>Duluth, GA 30096</p>
      <ul>
        <li>
          <svg viewBox="0 0 12 12" aria-hidden="true"><path d="M2 1h3l1 3-2 1a7 7 0 0 0 3 3l1-2 3 1v3c-6 1-10-3-9-9z"/></svg>
          770.415.2983
        </li>
        <li>
          <svg viewBox="0 0 12 12" aria-hidden="true"><rect x="3" y="0" width="6" height="4"/><rect x="0" y="5" width="12" height="5" rx="1"/><rect x="3" y="9" width="6" height="3"/></svg>
          770.581.4096
        </li>
        <li>
          <svg viewBox="0 0 12 12" aria-hidden="true"><circle cx="6" cy="6" r="6"/><path d="M0 6h12M6 0v12M2 2.5q4 2 8 0M2 9.5q4-2 8 0" stroke="#1d1e21" stroke-width="0.8" fill="none"/></svg>
          brightfernwellness.net
        </li>
        <li>
          <svg viewBox="0 0 12 12" aria-hidden="true"><path d="M0 2h12v8H0z M1 3l5 4 5-4" stroke="#1d1e21" stroke-width="1"/></svg>
          drgeraldwhitcombe@quillmarsh.net
        </li>
      </ul>
    </div>
  </section>
</body>
</html>
```